Business Card Design needed for start up company Halvora

In need of a new business card designed for a start up company based in Sydney, Halvora is a new start up innovative Company, our mission it to make property accessible for everyday Australian and to become the leading Real Estate platform in Australia. We want it to be fresh and clean.

Industry/Entity Type

Financial

Contact Information for Business Card

Section for Name
Section for Title

HALVORA - The Strength of Pooling
Mobile:
Direct:

Font styles to use
Sans Serif

Colors
33a6d7
0692cd
0255a3
ffffff

Requirements
Must have
• Logo, all business card details

```html
<!DOCTYPE html>
<html lang="en">
<head>
<meta charset="UTF-8">
<title>Halvora Business Card</title>
<link href="https://fonts.googleapis.com/css2?family=Montserrat:wght@800&family=Open+Sans:wght@400;600;700&display=swap" rel="stylesheet">
<style>
  :root {
    --sky: #5bc0ec;
    --sky-light: #33a6d7;
    --azure: #0692cd;
    --navy: #0255a3;
    --white: #ffffff;
    --ink: #4a4a4a;
    --backdrop: #2b2b2d;
  }
  html, body {
    margin: 0;
    width: 1200px;
    height: 1000px;
    overflow: hidden;
    background: var(--backdrop);
  }
  .canvas {
    position: relative;
    width: 1200px;
    height: 1000px;
  }
  .card {
    position: absolute;
    left: 325px;
    width: 550px;
    height: 314px;
    border-radius: 26px;
    overflow: hidden;
    box-shadow: 0 14px 30px rgba(0,0,0,0.45);
  }
  .card--front {
    top: 130px;
    background: linear-gradient(135deg, #4fb9ea 0%, #62c4ee 50%, #4cb6e8 100%);
  }
  .card--back {
    top: 520px;
    background: var(--white);
  }

  /* front */
  .front-brand {
    position: absolute;
    left: 105px;
    top: 112px;
    display: flex;
    align-items: center;
    gap: 14px;
  }
  .brand-dot {
    width: 62px;
    height: 62px;
    border-radius: 50%;
    background: var(--white);
  }
  .front-brand .brand-name {
    font-family: "Montserrat", sans-serif;
    font-weight: 800;
    font-size: 64px;
    letter-spacing: -1px;
    color: var(--white);
    line-height: 1;
  }
  .front-tagline {
    position: absolute;
    right: 70px;
    top: 196px;
    font-family: "Open Sans", sans-serif;
    font-size: 12px;
    letter-spacing: 3px;
    color: var(--white);
  }

  /* back */
  .side-band {
    position: absolute;
    left: 0;
    top: 0;
    width: 150px;
    height: 314px;
  }
  .back-brand {
    position: absolute;
    left: 34px;
    top: 58px;
    display: flex;
    align-items: center;
    gap: 12px;
  }
  .back-brand .brand-dot {
    width: 78px;
    height: 78px;
    background: var(--white);
    box-sizing: border-box;
    border: 5px solid var(--sky-light);
  }
  .back-brand .brand-name {
    font-family: "Montserrat", sans-serif;
    font-weight: 800;
    font-size: 58px;
    letter-spacing: -1px;
    color: var(--navy);
    line-height: 1;
  }
  .person {
    position: absolute;
    left: 150px;
    top: 148px;
    font-family: "Open Sans", sans-serif;
  }
  .person-name {
    font-weight: 700;
    font-size: 19px;
    color: var(--sky-light);
    letter-spacing: 0.5px;
    margin: 0;
  }
  .person-title {
    font-weight: 600;
    font-size: 14px;
    color: var(--ink);
    margin: 0;
  }
  .rule {
    width: 32px;
    height: 3px;
    background: var(--sky-light);
    margin: 8px 0 10px;
  }
  .contact-list {
    list-style: none;
    margin: 0;
    padding: 0;
    font-size: 13px;
    color: var(--ink);
    line-height: 17px;
  }
  .contact-list li {
    display: flex;
    align-items: center;
    gap: 8px;
  }
  .contact-list svg { width: 11px; height: 11px; fill: var(--azure); }
  .address {
    margin: 6px 0 0 19px;
    font-size: 13px;
    line-height: 17px;
    color: var(--ink);
  }
  .website {
    position: absolute;
    right: 26px;
    top: 150px;
    display: flex;
    align-items: center;
    gap: 6px;
    font-family: "Open Sans", sans-serif;
    font-size: 13px;
    color: var(--ink);
  }
  .website strong { color: var(--navy); font-weight: 600; }
  .website svg { width: 13px; height: 13px; }
</style>
</head>
<body>
<main class="canvas">

  <section class="card card--front" aria-label="Front of card">
    <div class="front-brand">
      <span class="brand-dot"></span>
      <span class="brand-name">HALVORA</span>
    </div>
    <p class="front-tagline">The Strength of Pooling</p>
  </section>

  <section class="card card--back" aria-label="Back of card">
    <svg class="side-band" viewBox="0 0 150 314" preserveAspectRatio="none" aria-hidden="true">
      <polygon points="0,0 55,0 118,314 0,314" fill="#5bc0ec"/>
    </svg>

    <div class="back-brand">
      <span class="brand-dot"></span>
      <span class="brand-name">HALVORA</span>
    </div>

    <div class="person">
      <p class="person-name">AARON BLAKE</p>
      <p class="person-title">Director</p>
      <div class="rule"></div>
      <ul class="contact-list">
        <li>
          <svg viewBox="0 0 24 24"><path d="M6.6 10.8a15.1 15.1 0 0 0 6.6 6.6l2.2-2.2a1 1 0 0 1 1-.25 11.4 11.4 0 0 0 3.6.57 1 1 0 0 1 1 1V20a1 1 0 0 1-1 1A17 17 0 0 1 3 4a1 1 0 0 1 1-1h3.5a1 1 0 0 1 1 1c0 1.25.2 2.45.57 3.57a1 1 0 0 1-.25 1z"/></svg>
          000 123 456 789
        </li>
        <li>
          <svg viewBox="0 0 24 24"><path d="M7 1h10a2 2 0 0 1 2 2v18a2 2 0 0 1-2 2H7a2 2 0 0 1-2-2V3a2 2 0 0 1 2-2zm0 3v14h10V4zm5 15.5a1 1 0 1 0 0 2 1 1 0 0 0 0-2z"/></svg>
          000 222 3334
        </li>
        <li>
          <svg viewBox="0 0 24 24"><path d="M2 5h20v14H2zm2 2v.5l8 5 8-5V7zm0 2.8V17h16V9.8l-8 5z"/></svg>
          urname@email.com
        </li>
      </ul>
      <p class="address">Your Street Address,<br>Sydney, 1234</p>
    </div>

    <div class="website">
      <svg viewBox="0 0 24 24" aria-hidden="true">
        <circle cx="12" cy="12" r="10" fill="none" stroke="#0255a3" stroke-width="2"/>
        <ellipse cx="12" cy="12" rx="4" ry="10" fill="none" stroke="#0255a3" stroke-width="2"/>
        <line x1="2" y1="12" x2="22" y2="12" stroke="#0255a3" stroke-width="2"/>
      </svg>
      <span>www.<strong>websitename</strong>.com</span>
    </div>
  </section>

</main>
</body>
</html>
```